Verlindo Magician

I want the business card for my business to give to people who watch that later I will be employed to show magic here is my website http://www.balsamomagicien.com/I want the interesting design , i am very opened for formal and informal, I watch a lot of design so don't stick to the common shape and form but i hope it can also be produced the thing to write on will be the same as in picture that i will upload , i also will upload the logo for you that so can be easy to useDenis CostilleMagicianMAGICIAN BALSAMO 17 rue des Tilleuls - 25000 BESANÇON contact@verlindoillusions.example tel. 0381 946 157 tel. 0674 219 503

```html
<!DOCTYPE html>
<html lang="fr">
<head>
<meta charset="utf-8">
<title>Verlindo Magician – Business Card</title>
<link href="https://fonts.googleapis.com/css2?family=Jost:wght@300;400;500;700&display=swap" rel="stylesheet">
<style>
  :root {
    --backdrop: #2a2a2c;
    --card: #1e1f22;
    --ink: #f4f4f4;
    --accent: #d8302b;
    --rule: #5a5b60;
    --pattern-a: #25262a;
    --pattern-b: #1c1d20;
    --figure-top: #ededed;
    --figure-bottom: #c4c4c4;
  }
  * { box-sizing: border-box; margin: 0; padding: 0; }
  html, body {
    width: 1200px; height: 1108px; overflow: hidden;
    background: var(--backdrop);
    font-family: "Jost", sans-serif;
    color: var(--ink);
  }
  .stage {
    position: relative; width: 1200px; height: 1108px;
    display: flex; justify-content: center; align-items: center; gap: 60px;
  }
  .card {
    position: relative;
    width: 420px; height: 640px;
    background: var(--card);
    border-radius: 22px;
    box-shadow: 0 18px 40px rgba(0,0,0,.45);
    overflow: hidden;
  }
  /* Front */
  .card--front {
    display: flex; flex-direction: column; align-items: center;
    text-align: center; padding-top: 150px;
  }
  .brand-name {
    font-weight: 300; font-size: 58px; letter-spacing: 3px; line-height: 1;
  }
  .holder { margin-top: 96px; }
  .holder-name {
    font-weight: 700; font-size: 27px; color: var(--accent);
    letter-spacing: .5px; text-transform: uppercase; line-height: 1.05;
  }
  .holder-role { font-weight: 400; font-size: 19px; line-height: 1.1; }
  .rule { width: 170px; height: 1px; background: var(--rule); margin: 14px auto; }
  .contacts { list-style: none; font-size: 19px; line-height: 1.22; font-weight: 400; }
  .contacts .label { color: var(--accent); font-weight: 700; margin-right: 4px; }
  .studio-name {
    font-weight: 700; font-size: 19px; color: var(--accent);
    text-transform: uppercase; line-height: 1.2;
  }
  .studio-address { font-size: 19px; line-height: 1.2; }
  /* Back */
  .card--back { display: flex; flex-direction: column; align-items: center; }
  .back-pattern {
    position: absolute; inset: 0;
    background: linear-gradient(160deg, var(--pattern-a), var(--pattern-b));
  }
  .portrait {
    position: relative; margin-top: 290px;
    width: 190px; height: 230px;
    background: linear-gradient(180deg, var(--figure-top) 0%, var(--figure-bottom) 100%);
    border-radius: 80px 80px 14px 14px;
  }
  .back-brand {
    position: relative; margin-top: 18px;
    font-weight: 300; font-size: 44px; letter-spacing: 3px; line-height: 1;
  }
</style>
</head>
<body>
<main class="stage">
  <article class="card card--front">
    <div class="brand-name">VERLINDO</div>
    <section class="holder">
      <h1 class="holder-name">Marc Ravoulet</h1>
      <p class="holder-role">Magician</p>
      <div class="rule"></div>
      <ul class="contacts">
        <li><span class="label">P:</span>0400 946 157</li>
        <li><span class="label">P:</span>0674 219 503</li>
        <li><span class="label">E:</span>contact@verlindoillusions.example</li>
        <li><span class="label">W:</span>www.verlindoillusions.example</li>
      </ul>
      <div class="rule"></div>
      <p class="studio-name">Magician Verlindo</p>
      <p class="studio-address">17 rue des Tilleuls - 39170 VAUDRELLE</p>
    </section>
  </article>

  <article class="card card--back">
    <div class="back-pattern" role="img" aria-label="Faint repeated brand-name pattern background"></div>
    <div class="portrait" role="img" aria-label="White silhouette illustration of the magician holding a playing card"></div>
    <div class="back-brand">VERLINDO</div>
  </article>
</main>
</body>
</html>
```